Creative, fresh business card design for Ripplecraft Facades

We need a fresh, creative business card design for Ripplecraft Facades. We are the manufacturer of Ripplecraft Facades in Australia. Wall panels are 2400 x 1200mm panels made from MDF and feature 3D patterns on the face of the panel. The colours to be used are green, silver/grey and white RGB
Red 187
Green 207
Blue 65.

An idea is to possibly use a watermark of one of our designs as a background (like on the "Grids" design on the left hand side of page 2 of our brochure).

Target Market(s)

Interior designers, architects, builders and home renovators

Industry/Entity Type

Business

Contact Information for Business Card

Details to go on the card are:
Our logo (attached),
Slogan: "Decorative panels for interiors and exteriors",
Contact name,
Position,
Mobile phone number,
Business address,
Business phone,
Business fax,
Website and
Email address.

I have attached a few images of our panels and our brochure for reference.

The colours of the business card should feature our logo colours which are: RGB
Red 187
Green 207
Blue 65

Requirements
Must have
• Very modern fonts and design. Some of the designs shown especially the "Prisms" design which is a popular design.
Nice to have
• Creative but simple design. Very contemporary.
Should not have
• Anything ornate or old fashioned.

```html
<!DOCTYPE html>
<html lang="en">
<head>
<meta charset="utf-8">
<title>Ripplecraft Facades – Business Card Concepts</title>
<link rel="stylesheet" href="https://fonts.googleapis.com/css2?family=Arimo:wght@400;700&display=swap">
<style>
:root{
  --stage:#231f20;
  --lime:#bbcf41;
  --charcoal:#4a4a4c;
  --charcoal-deep:#2f2e30;
  --silver:#8f8f91;
  --paper:#ffffff;
  --ink:#3c3c3e;
  --ink-soft:#6a6a6c;
}
*{box-sizing:border-box;margin:0;padding:0}
html,body{width:1136px;height:1200px;overflow:hidden;background:var(--stage)}
body{position:relative;font-family:"Arimo",Arial,sans-serif;color:var(--ink)}
.side-label{position:absolute;color:var(--paper);font-weight:700;font-size:21px;letter-spacing:.5px}
.card{position:absolute;width:485px;height:296px;overflow:hidden;background:var(--paper)}
.texture-light{position:absolute;background:linear-gradient(135deg,#fafafa 0%,#e6e6e7 35%,#f7f7f7 55%,#e1e1e2 80%,#f4f4f4 100%)}
.texture-dark{position:absolute;background:linear-gradient(135deg,#3a393b 0%,#2e2d2f 50%,#363537 100%)}
.band-dark{position:absolute;left:0;width:100%;background:var(--charcoal)}
.bar-lime{position:absolute;left:0;width:100%;background:var(--lime)}
.brand{position:absolute;display:flex;align-items:center;gap:8px}
.brand-mark{width:24px;height:24px;background:var(--lime);flex:none}
.brand-name{font-weight:700;font-size:19px;color:var(--ink);white-space:nowrap}
.slogan{position:absolute;font-size:12.5px;letter-spacing:1.6px;color:var(--silver);line-height:1.15;text-align:center}
.website{position:absolute;font-size:16px;color:var(--ink)}
.person{position:absolute}
.person-name{font-weight:700;font-size:17px;color:var(--ink);line-height:1.05}
.person-role{font-size:14px;color:var(--ink-soft);margin-top:2px}
.on-dark .person-name{color:var(--paper)}
.on-dark .person-role{color:#d8d8d8}
.contacts{position:absolute;list-style:none}
.contacts li{display:flex;align-items:flex-start;gap:8px;font-size:13.5px;line-height:1.2;color:var(--ink);white-space:nowrap}
.contacts.on-dark li{color:var(--paper)}
.contacts svg{width:14px;height:14px;flex:none;margin-top:1px;stroke:var(--lime);fill:none;stroke-width:1.6}
.contacts.compact li{font-size:12.5px}
.socials{position:absolute;display:flex;gap:9px}
.socials span{width:32px;height:32px;border-radius:50%;background:var(--charcoal)}
.badge-icon{width:22px;height:22px;border-radius:50%;background:var(--lime);display:flex;align-items:center;justify-content:center;flex:none}
.badge-icon svg{stroke:var(--paper);width:13px;height:13px;margin:0}
.contacts.big li{font-size:13.5px;align-items:center;gap:6px}
.logo-frame{position:absolute;background:var(--paper);padding:10px 12px}
</style>
</head>
<body>

<svg width="0" height="0" style="position:absolute" aria-hidden="true">
  <defs>
    <symbol id="i-mobile" viewBox="0 0 16 16"><rect x="4" y="1.5" width="8" height="13" rx="1.5"/><line x1="7" y1="12" x2="9" y2="12"/></symbol>
    <symbol id="i-pin" viewBox="0 0 16 16"><path d="M8 15s5-5.2 5-8.5A5 5 0 0 0 3 6.5C3 9.8 8 15 8 15z"/><circle cx="8" cy="6.5" r="1.8"/></symbol>
    <symbol id="i-phone" viewBox="0 0 16 16"><path d="M2 6c0-2 2-3 6-3s6 1 6 3l-2 1-1-2H5L4 7z"/><rect x="3.5" y="8" width="9" height="5.5" rx="1"/></symbol>
    <symbol id="i-fax" viewBox="0 0 16 16"><rect x="2" y="6" width="12" height="8" rx="1"/><path d="M5 6V2h6v4"/><line x1="5" y1="9" x2="11" y2="9"/></symbol>
    <symbol id="i-mail" viewBox="0 0 16 16"><circle cx="8" cy="8" r="2.6"/><path d="M10.6 8v1.2a1.8 1.8 0 0 0 3.4.8A6.5 6.5 0 1 0 11 13.6"/></symbol>
  </defs>
</svg>

<!-- Row 1 -->
<div class="side-label" style="left:69px;top:64px">FRONT</div>
<section class="card" style="left:69px;top:99px">
  <div role="img" aria-label="Photo of a reception lounge with a feature wall" style="position:absolute;left:0;top:0;width:220px;height:100%;background:linear-gradient(160deg,#d9d4cc 0%,#8a6e52 45%,#5b3f2a 75%,#3e3a2e 100%)"></div>
  <div class="texture-light" role="img" aria-label="Faceted wall panel texture" style="left:220px;top:0;right:0;bottom:0"></div>
  <div class="brand" style="left:244px;top:48px"><span class="brand-mark"></span><span class="brand-name">Ripplecraft Facades</span></div>
  <p class="slogan" style="left:232px;top:86px;width:240px">decorative panels for<br>interiors &amp; landscapes</p>
  <p class="website" style="left:244px;top:266px">www.ripplecraftfacades.com.au</p>
</section>

<div class="side-label" style="left:580px;top:58px">BACK</div>
<section class="card" style="left:580px;top:95px">
  <div class="texture-light" role="img" aria-label="Faceted wall panel texture" style="inset:0"></div>
  <div class="brand" style="left:31px;top:36px"><span class="brand-mark"></span><span class="brand-name">Ripplecraft Facades</span></div>
  <div class="person" style="left:29px;top:226px">
    <p class="person-name">MARA LINDQVIST</p>
    <p class="person-role">Owner,</p>
  </div>
  <ul class="contacts compact" style="left:262px;top:128px">
    <li style="margin-bottom:6px"><svg><use href="#i-mobile"/></svg>0400 555 218</li>
    <li style="margin-bottom:6px"><svg><use href="#i-pin"/></svg>14 Kestrel Lane,<br>Marlow Park NSW 2199</li>
    <li style="margin-bottom:6px"><svg><use href="#i-phone"/></svg>02 9000 4811</li>
    <li style="margin-bottom:6px"><svg><use href="#i-fax"/></svg>02 9000 4812</li>
    <li><svg><use href="#i-mail"/></svg>sales@ripplecraftfacades.com.au</li>
  </ul>
  <div class="bar-lime" style="bottom:0;height:13px"></div>
</section>

<!-- Row 2 -->
<div class="side-label" style="left:69px;top:428px">BACK</div>
<section class="card" style="left:69px;top:458px">
  <div class="texture-light" role="img" aria-label="Faceted wall panel texture" style="inset:0"></div>
  <div class="band-dark" style="top:48px;height:165px"></div>
  <div class="bar-lime" style="top:213px;height:25px"></div>
  <div class="person on-dark" style="left:28px;top:110px">
    <p class="person-name">MARA<br>LINDQVIST</p>
    <p class="person-role">Owner,</p>
  </div>
  <ul class="contacts on-dark" style="left:234px;top:66px">
    <li style="margin-bottom:8px"><svg><use href="#i-mobile"/></svg>0400 555 218</li>
    <li style="margin-bottom:8px"><svg><use href="#i-pin"/></svg>14 Kestrel Lane,<br>Marlow Park NSW 2199</li>
    <li style="margin-bottom:8px"><svg><use href="#i-phone"/></svg>02 9000 4811</li>
    <li style="margin-bottom:8px"><svg><use href="#i-fax"/></svg>02 9000 4812</li>
    <li><svg><use href="#i-mail"/></svg>sales@ripplecraftfacades.com.au</li>
  </ul>
  <div class="socials" style="right:20px;top:247px"><span></span><span></span><span></span><span></span></div>
</section>

<div class="side-label" style="left:580px;top:428px">BACK</div>
<section class="card" style="left:580px;top:458px">
  <div class="texture-light" role="img" aria-label="Faceted wall panel texture" style="inset:0"></div>
  <div class="person" style="left:0;top:12px;width:100%;text-align:center">
    <p class="person-name">MARA LINDQVIST</p>
    <p class="person-role">Owner,</p>
  </div>
  <div class="band-dark" style="top:62px;height:164px"></div>
  <div class="bar-lime" style="top:226px;height:11px"></div>
  <div class="logo-frame" style="left:30px;top:122px">
    <div class="brand" style="position:static"><span class="brand-mark" style="width:18px;height:18px"></span><span class="brand-name" style="font-size:15px">Ripplecraft Facades</span></div>
  </div>
  <ul class="contacts on-dark" style="left:232px;top:80px">
    <li style="margin-bottom:7px"><svg><use href="#i-mobile"/></svg>0400 555 218</li>
    <li style="margin-bottom:7px"><svg><use href="#i-pin"/></svg>14 Kestrel Lane,<br>Marlow Park NSW 2199</li>
    <li style="margin-bottom:7px"><svg><use href="#i-phone"/></svg>02 9000 4811</li>
    <li style="margin-bottom:7px"><svg><use href="#i-fax"/></svg>02 9000 4812</li>
    <li><svg><use href="#i-mail"/></svg>sales@ripplecraftfacades.com.au</li>
  </ul>
  <div class="socials" style="left:159px;top:247px"><span></span><span></span><span></span><span></span></div>
</section>

<!-- Row 3 -->
<section class="card" style="left:69px;top:802px">
  <div role="img" aria-label="Faint cube panel pattern" style="position:absolute;inset:0;background:linear-gradient(180deg,#ffffff 0%,#f3f3f3 100%)"></div>
  <div class="brand" style="left:140px;top:84px"><span class="brand-mark"></span><span class="brand-name">Ripplecraft Facades</span></div>
  <p class="slogan" style="left:122px;top:183px;width:240px">decorative panels for<br>interiors &amp; landscapes</p>
  <p class="website" style="left:116px;top:250px">www.ripplecraftfacades.com.au</p>
</section>
<div class="side-label" style="left:69px;top:1110px">FRONT</div>

<section class="card" style="left:580px;top:802px;background:var(--charcoal-deep)">
  <div class="texture-dark" role="img" aria-label="Faint cube panel pattern" style="inset:0"></div>
  <div class="person on-dark" style="left:28px;top:24px">
    <p class="person-name" style="color:var(--lime)">MARA LINDQVIST</p>
    <p class="person-role">Owner,</p>
  </div>
  <ul class="contacts on-dark big" style="left:222px;top:102px">
    <li style="margin-bottom:14px"><span class="badge-icon"><svg><use href="#i-mobile"/></svg></span>0400 555 218</li>
    <li style="margin-bottom:8px"><span class="badge-icon"><svg><use href="#i-pin"/></svg></span>14 Kestrel Lane,<br>Marlow Park NSW 2199</li>
    <li style="margin-bottom:7px"><span class="badge-icon"><svg><use href="#i-phone"/></svg></span>02 9000 4811</li>
    <li style="margin-bottom:7px"><span class="badge-icon"><svg><use href="#i-fax"/></svg></span>02 9000 4812</li>
    <li><span class="badge-icon"><svg><use href="#i-mail"/></svg></span>sales@ripplecraftfacades.com.au</li>
  </ul>
  <div class="bar-lime" style="bottom:0;height:10px"></div>
</section>
<div class="side-label" style="left:580px;top:1118px">BACK</div>

</body>
</html>
```